Business cards and stationary design

We just completed the design of our new logo and we need to print new business cards and letterhead for our nonprofit. We are looking for a fresh new design that shows off our new logo. On letterhead, we must have a column on the right or left to include our Board of Directors (up to 45 names) (see attachment)

Industry/Entity Type

Non-Profit

Contact Information for Business Card

Standard business card with name, title, Company name, mailing address phone numbers, email address and website. Tagline on back "Bringing the homeless home"

Font styles to use
Sans Serif

Requirements
Must have
• include pertinent information above
• new logo
• fonts compatible with logo
• should use logo colors only
Nice to have
• tag lines

```html
<!DOCTYPE html>
<html lang="en">
<head>
<meta charset="utf-8">
<title>Harbor Home Alliance — Business Card</title>
<link rel="stylesheet" href="https://fonts.googleapis.com/css2?family=Michroma&family=Arimo:wght@400&display=swap">
<style>
  :root {
    --teal: #0b7fa2;
    --red: #d42a2e;
    --yellow: #f2b632;
    --paper: #f9f9f9;
    --ink: #555555;
    --backdrop: #e2e2e2;
    --white: #ffffff;
  }
  * { box-sizing: border-box; margin: 0; padding: 0; }
  html, body {
    width: 1200px; height: 582px; overflow: hidden;
    background: var(--backdrop);
  }
  .canvas { position: relative; width: 1200px; height: 582px; }

  .card {
    position: absolute; top: 158px;
    width: 463px; height: 264px;
  }
  .card--front { left: 122px; background: var(--paper); }
  .card--back { left: 602px; background: var(--teal); }

  /* Front */
  .brand {
    position: absolute; right: 25px; top: 72px;
    display: flex; align-items: center; gap: 8px;
  }
  .brand__mark { width: 12px; height: 12px; background: var(--yellow); }
  .brand__name {
    font-family: "Michroma", sans-serif;
    font-size: 13px; letter-spacing: 1.5px;
    color: var(--teal);
  }
  .brand__rule {
    position: absolute; right: 25px; top: 106px;
    width: 196px; height: 1px; background: var(--red);
  }

  .person { position: absolute; left: 25px; top: 155px; }
  .person__name {
    font-family: "Michroma", sans-serif;
    font-size: 15px; letter-spacing: 1.2px;
    color: var(--teal); line-height: 18px;
  }
  .person__title {
    font-family: "Michroma", sans-serif;
    font-size: 9px; letter-spacing: 1.2px;
    color: var(--red); line-height: 12px; margin-top: 1px;
  }

  .divider {
    position: absolute; left: 25px; top: 190px;
    width: 413px; height: 2px; display: flex; gap: 2px;
  }
  .divider span { flex: 1; }
  .divider .teal { background: var(--teal); }
  .divider .red { background: var(--red); }
  .divider .yellow { background: var(--yellow); }

  .contacts {
    position: absolute; left: 25px; top: 201px;
    list-style: none;
    font-family: "Arimo", sans-serif; font-size: 11px;
    color: var(--ink);
  }
  .contacts li {
    display: flex; align-items: center; gap: 6px;
    height: 15px;
  }
  .contacts svg { width: 10px; height: 10px; fill: var(--teal); }

  .address {
    position: absolute; right: 25px; top: 201px;
    font-family: "Arimo", sans-serif; font-size: 11px;
    color: var(--ink); text-align: right; font-style: normal;
    line-height: 15px;
  }

  /* Back */
  .back-brand {
    position: absolute; left: 0; right: 0; top: 100px;
    display: flex; justify-content: center; align-items: center; gap: 12px;
  }
  .back-brand__mark { width: 18px; height: 18px; background: var(--white); }
  .back-brand__name {
    font-family: "Michroma", sans-serif;
    font-size: 20px; letter-spacing: 2px;
    color: var(--white);
  }
  .back-web {
    position: absolute; left: 0; right: 0; top: 223px;
    text-align: center;
    font-family: "Michroma", sans-serif;
    font-size: 9px; letter-spacing: 3.5px;
    color: var(--white);
  }
</style>
</head>
<body>
<main class="canvas">
  <section class="card card--front" aria-label="Business card front">
    <div class="brand">
      <span class="brand__mark"></span>
      <span class="brand__name">HARBOR HOME ALLIANCE</span>
    </div>
    <div class="brand__rule"></div>

    <div class="person">
      <p class="person__name">DANA WHITFIELD</p>
      <p class="person__title">CEO/FOUNDER</p>
    </div>

    <div class="divider"><span class="teal"></span><span class="red"></span><span class="yellow"></span></div>

    <ul class="contacts">
      <li>
        <svg viewBox="0 0 10 10" aria-hidden="true"><path d="M2 0.5 L3.6 2.6 L2.7 3.6 C3.3 5 4.9 6.6 6.4 7.3 L7.4 6.4 L9.5 8 L8.4 9.5 C4.5 9.2 0.8 5.5 0.5 1.6 Z"/></svg>
        <span>555 210 4471</span>
      </li>
      <li>
        <svg viewBox="0 0 10 10" aria-hidden="true"><path d="M0.5 2 H9.5 V8 H0.5 Z M1 2.5 L5 5.5 L9 2.5" stroke="#f9f9f9" stroke-width="0.7"/></svg>
        <span>dana@harborhome.org</span>
      </li>
      <li>
        <svg viewBox="0 0 10 10" aria-hidden="true"><circle cx="5" cy="5" r="4.5"/><path d="M0.5 5 H9.5 M5 0.5 C3 3 3 7 5 9.5 M5 0.5 C7 3 7 7 5 9.5" stroke="#f9f9f9" stroke-width="0.6" fill="none"/></svg>
        <span>www.harborhome.org</span>
      </li>
    </ul>

    <address class="address">
      Harbor Home Alliance<br>
      1420 Birchwood Road<br>
      Fairview, Alaska 99512
    </address>
  </section>

  <section class="card card--back" aria-label="Business card back">
    <div class="back-brand">
      <span class="back-brand__mark"></span>
      <span class="back-brand__name">HARBOR HOME ALLIANCE</span>
    </div>
    <p class="back-web">WWW.HARBORHOME.ORG</p>
  </section>
</main>
</body>
</html>
```